BOLD & MINIMALIST DESIGN NEEDED

We want a very bold but minimalistic business card design that is impactful and utilizes both sides of the business card. Our current logo is included for your use.

We want bold fonts and good use of negative space. We don't want the logo to overpower the design.

Target Market(s)

Professionals who are building new commercial buildings.

Industry/Entity Type

Construction

Contact Information for Business Card

Name, Title, email, office phone, cell phone, website

Font styles to use
Serif
Sans Serif

Requirements
Must have
• Bold design!

```html
<!DOCTYPE html>
<html lang="en">
<head>
<meta charset="utf-8">
<title>Ridgecrest Builders — Business Card</title>
<link href="https://fonts.googleapis.com/css2?family=Open+Sans:wght@400;600;800&display=swap" rel="stylesheet">
<style>
  :root {
    --page: #ececec;
    --ink: #0d0d0d;
    --paper: #ffffff;
    --green: #7cc242;
    --grey: #6b6b6b;
  }
  * { margin: 0; padding: 0; box-sizing: border-box; }
  html, body { width: 1200px; height: 900px; overflow: hidden; background: var(--page); }
  body { font-family: "Open Sans", Arial, sans-serif; position: relative; }

  .card {
    position: absolute; left: 270px; width: 660px; height: 380px;
    border-radius: 24px; overflow: hidden;
    box-shadow: 0 10px 28px rgba(0,0,0,0.18);
  }
  .card--front { top: 50px; background: var(--paper); }
  .card--back { top: 470px; background: var(--ink); }

  /* front */
  .front__band { position: absolute; left: 0; bottom: 0; width: 380px; height: 150px; background: var(--ink); }
  .front__accent { position: absolute; right: 0; bottom: 0; width: 280px; height: 150px; background: var(--green); }
  .wordmark {
    display: flex; align-items: center; gap: 12px; white-space: nowrap;
    font-weight: 800; color: var(--ink); letter-spacing: 1px; text-transform: uppercase;
  }
  .wordmark__mark { background: var(--green); flex: none; }
  .front__wordmark { position: absolute; left: 44px; top: 36px; font-size: 30px; }
  .front__wordmark .wordmark__mark { width: 18px; height: 18px; }

  .person { position: absolute; right: 48px; top: 104px; text-align: right; }
  .person__name { color: var(--green); font-weight: 800; font-size: 24px; letter-spacing: 0.5px; text-transform: uppercase; }
  .person__role, .person__address { color: var(--grey); font-size: 17px; line-height: 1.35; }
  .person__role { font-weight: 600; margin-bottom: 6px; }

  .contact { position: absolute; left: 44px; bottom: 28px; list-style: none; }
  .contact__item { display: flex; align-items: center; gap: 10px; color: var(--paper); font-size: 16px; line-height: 1.75; }
  .contact__icon { width: 14px; height: 14px; flex: none; }

  /* back */
  .back__dome { position: absolute; left: 0; top: 0; width: 660px; height: 380px; }
  .back__wordmark { position: absolute; left: 56px; top: 226px; font-size: 34px; }
  .back__wordmark .wordmark__mark { width: 22px; height: 22px; }
</style>
</head>
<body>

<section class="card card--front" aria-label="Business card front">
  <div class="front__band"></div>
  <div class="front__accent"></div>

  <div class="wordmark front__wordmark">
    <span class="wordmark__mark"></span>
    <span class="wordmark__name">Ridgecrest Builders</span>
  </div>

  <div class="person">
    <p class="person__name">Daniel Carter</p>
    <p class="person__role">Managing Director</p>
    <p class="person__address">Your Address, City<br>State, Zip 0000</p>
  </div>

  <ul class="contact">
    <li class="contact__item">
      <svg class="contact__icon" viewBox="0 0 16 16" aria-hidden="true"><circle cx="8" cy="8" r="8" fill="#7cc242"/><path d="M5 4.5l1.6-.3.9 2-1 .8a5 5 0 002.5 2.5l.8-1 2 .9-.3 1.6c-3.6.2-6.7-2.9-6.5-6.5z" fill="#0d0d0d"/></svg>
      044-555 210 348
    </li>
    <li class="contact__item">
      <svg class="contact__icon" viewBox="0 0 16 16" aria-hidden="true"><circle cx="8" cy="8" r="8" fill="#7cc242"/><rect x="4" y="5" width="8" height="6" fill="#0d0d0d"/><path d="M4 5l4 3.5L12 5" stroke="#7cc242" fill="none"/></svg>
      hello@ridgecrestbuild.com
    </li>
    <li class="contact__item">
      <svg class="contact__icon" viewBox="0 0 16 16" aria-hidden="true"><circle cx="8" cy="8" r="8" fill="#7cc242"/><circle cx="8" cy="8" r="4.5" fill="none" stroke="#0d0d0d" stroke-width="1.3"/><path d="M3.5 8h9M8 3.5v9" stroke="#0d0d0d" stroke-width="1.1"/></svg>
      www.ridgecrestbuild.com
    </li>
  </ul>
</section>

<section class="card card--back" aria-label="Business card back">
  <svg class="back__dome" viewBox="0 0 660 380" aria-hidden="true">
    <path d="M0 380 L0 140 Q0 110 40 104 C260 70 560 120 640 380 Z" fill="#ffffff"/>
  </svg>
  <div class="wordmark back__wordmark">
    <span class="wordmark__mark"></span>
    <span class="wordmark__name">Ridgecrest Builders</span>
  </div>
</section>

</body>
</html>
```